Brintel Works - Fast, Efficient and Gas Mainteance for Domestic, Commercial and Industrial clients

We are in the process of purchasing a new business and would like to get a new logo and business card.
Business is a gas maintenance business that also does new gas installations.
Has been established since 1988.
Services include:
Install all types of gas appliances & equipment inc. hot water units
Maintain / repair / replace all types of gas appliances & equipment

Target Market(s)

Domestic, Commercial and Industrial clients

Industry/Entity Type

Business

Contact Information for Business Card

admin@brintelworks.com.au
07 3918 4726
Brintel Works PTY LTD

Logo Text

Gas Fitting & Plumbing Maintenance Specialists

Font styles to use
Sans Serif

Requirements
Must have
• Logo
• Business name, contact number, email address, web address
• Domestic | Commercial | Industrial Est Since 1988
Nice to have
• Possibly a black card with a flame logo to one side
Should not have
• Spelling errors

```html
<!DOCTYPE html>
<html lang="en">
<head>
<meta charset="utf-8">
<title>Brintel Works – Business Card</title>
<link rel="stylesheet" href="https://fonts.googleapis.com/css2?family=Source+Sans+3:wght@400;700&display=swap">
<style>
  :root {
    --stage: #161616;
    --card-white: #ffffff;
    --brand-red: #e8262a;
    --brand-orange: #f26a21;
    --brand-yellow: #fcd116;
  }
  html, body {
    margin: 0;
    width: 1200px;
    height: 900px;
    overflow: hidden;
    background: var(--stage);
  }
  .stage {
    position: relative;
    width: 1200px;
    height: 900px;
  }
  .card {
    position: absolute;
    top: 170px;
    width: 347px;
    height: 561px;
    font-family: "Source Sans 3", sans-serif;
  }
  .card-front {
    left: 259px;
    background: var(--card-white);
    color: var(--brand-red);
    text-align: center;
  }
  .card-back {
    left: 631px;
    background: linear-gradient(to bottom, var(--brand-yellow) 0%, var(--brand-orange) 55%, var(--brand-red) 100%);
  }
  .accent-band {
    position: absolute;
    left: 102px;
    width: 143px;
    height: 30px;
  }
  .accent-band-top {
    top: 0;
    background: linear-gradient(to bottom, var(--brand-yellow), var(--brand-red));
  }
  .accent-band-bottom {
    bottom: 0;
    height: 28px;
    background: linear-gradient(to bottom, var(--brand-red), var(--brand-yellow));
  }
  .brand-dot {
    position: absolute;
    left: 143px;
    top: 100px;
    width: 60px;
    height: 60px;
    border-radius: 50%;
    background: var(--brand-red);
  }
  .brand-name {
    position: absolute;
    left: 0;
    right: 0;
    top: 198px;
    margin: 0;
    font-size: 32px;
    font-weight: 700;
    line-height: 1;
  }
  .brand-suffix {
    position: absolute;
    left: 0;
    right: 0;
    top: 238px;
    margin: 0;
    font-size: 12px;
    font-weight: 700;
    letter-spacing: 2px;
    line-height: 1;
  }
  .contact-list {
    position: absolute;
    left: 0;
    right: 0;
    top: 285px;
    margin: 0;
    padding: 0;
    list-style: none;
    font-size: 16px;
    line-height: 20px;
  }
  .contact-list li {
    display: flex;
    justify-content: center;
    align-items: center;
    gap: 7px;
  }
  .contact-icon {
    width: 11px;
    height: 11px;
    flex: none;
  }
  .address, .sectors {
    position: absolute;
    left: 0;
    right: 0;
    margin: 0;
    font-size: 16px;
    line-height: 20px;
  }
  .address { top: 370px; }
  .sectors { top: 436px; }
  .back-name {
    position: absolute;
    left: 0;
    right: 0;
    top: 256px;
    margin: 0;
    text-align: center;
    font-size: 38px;
    font-weight: 700;
    color: var(--brand-red);
  }
</style>
</head>
<body>
<main class="stage">
  <section class="card card-front" aria-label="Business card front">
    <div class="accent-band accent-band-top"></div>
    <div class="brand-dot"></div>
    <h1 class="brand-name">Brintel Works</h1>
    <p class="brand-suffix">PTY LTD</p>
    <ul class="contact-list">
      <li>
        <svg class="contact-icon" viewBox="0 0 12 12" aria-hidden="true"><path fill="#f26a21" d="M2.5 1l2 2.2-1 1.3c.7 1.5 1.8 2.6 3.2 3.3l1.3-1 2.2 2-1 2C4.8 10.6 1.4 7.2 1 2.3z"/></svg>
        <span>07 3918 4726</span>
      </li>
      <li>
        <svg class="contact-icon" viewBox="0 0 12 12" aria-hidden="true"><rect x="1" y="3" width="10" height="7" fill="#f26a21"/><path d="M1 3l5 4 5-4" fill="none" stroke="#fff" stroke-width="1"/></svg>
        <span>admin@brintelworks.com.au</span>
      </li>
      <li>
        <svg class="contact-icon" viewBox="0 0 12 12" aria-hidden="true"><circle cx="6" cy="6" r="5" fill="#f9a21b"/><path d="M1 6h10M6 1c-2.5 3-2.5 7 0 10M6 1c2.5 3 2.5 7 0 10" fill="none" stroke="#fff" stroke-width=".8"/></svg>
        <span>www.brintelworks.com.au</span>
      </li>
    </ul>
    <p class="address">12345, Address Goes Here<br>Country Name, 123456.</p>
    <p class="sectors">Domestic | Commercial<br>Industrial Est Since 1988</p>
    <div class="accent-band accent-band-bottom"></div>
  </section>

  <section class="card card-back" aria-label="Business card back">
    <p class="back-name">Brintel Works</p>
  </section>
</main>
</body>
</html>
```